Maple Beacon Website

We are starting a marketing company and to do that we need a website! We want a website that will inspire and persuade to bring out the awesomeness in our clients.
What we want to see:
- Inspirational and persuasive imagery that relate to Branding.
- No cliche images eg. business man, suits and hand shakes
- We want to transform and educate our clients.
- We want to show them the path and would like our website to really act as a guide that guides them step by step through our process.
- We want the portray that we are an investment but not have a pretentious way to it. We put our heart into every project and that is how we treat our clients.
-When you submit your design please include what platform you have created for. Preference would be Wordpress or Joobla.

We have included the psd file for the wire frame, logo files, font files, site map and a link to a video we create to give you more information on what we would like to see. http://clipvault.example/t/qk82LmZpr

Feel free to make small modification to the logos if you think it will improve it. Your creativity and advice is most welcome.
Updates

One thing we forgot. We would like to have our contact information near the top of the website as well as at the bottom.  Here is out contact info:

Email: info@maplebeacon.example
Phone: 587-555-0142

Project Deadline Extended
Reason: As we are new with the platform and that we want to optimize our results, we decided to extend the deadline by 15 days. Thanks!

Target Market(s)

28-60, Male and Female, Oil field, Local Businesses, Dentists, Chiropractors, Hair salon, Construction/Renovation, Events etc

Industry/Entity Type

Investment

Requirements
Must have
• - 4 Inspirational and persuasive Imagery for the top portion of the website
- Must have a feel as if your not on a website an example of this is linked below.
http://www.artbidhub.example/design/402957/web-design-by-lena-torvik
Nice to have
• - Creative advice from you.
- Creative buttons for Get Free Quote and Subscribe buttons. Something out of the box that draws peoples attention. eg. a 'B' button. Just and example but still something related to branding.
Should not have
• No Cliches

```html
<!DOCTYPE html>
<html lang="en">
<head>
<meta charset="utf-8">
<title>Maple Beacon</title>
<link rel="stylesheet" href="https://fonts.googleapis.com/css2?family=PT+Sans:wght@400;700&family=Arvo:wght@700&family=Carter+One&family=Tinos:ital,wght@1,700&family=Cinzel:wght@600&family=Arimo:wght@400&display=swap">
<style>
:root{
  --green:#5aa51e;
  --green-light:#9ad43a;
  --green-dark:#3f8612;
  --heading-green:#4b9a1c;
  --gray-dark:#4a4a4a;
  --gray-text:#8b8b8b;
  --gray-nav:#2f2f2f;
  --panel-top:#ffffff;
  --panel-bottom:#d9d9d9;
  --page:#fafafa;
  --white:#ffffff;
  --hero-dark:#0c0f26;
  --hero-mid:#2c3c4a;
  --hero-olive:#7f8456;
  --hero-light:#a9a468;
}
*{margin:0;padding:0;box-sizing:border-box}
html,body{width:1200px;height:953px;overflow:hidden;background:var(--page)}
.canvas{position:relative;width:1200px;height:953px;background:linear-gradient(#fdfdfd,#f6f6f6 70%,#ededed);font-family:"PT Sans",sans-serif}

.side-panel{position:absolute;left:35px;top:0;width:283px;height:374px;background:linear-gradient(var(--panel-top) 20%,var(--panel-bottom))}
.brand{position:absolute;left:22px;top:44px;display:flex;align-items:center;gap:10px}
.brand-mark{width:14px;height:14px;border-radius:50%;background:var(--green)}
.brand-name{font-family:"PT Sans",sans-serif;font-weight:700;font-size:29px;line-height:30px;color:var(--gray-dark);letter-spacing:1px}
.tagline{position:absolute;left:56px;top:116px;font-family:"PT Sans",sans-serif;font-style:italic;font-size:16px;color:var(--gray-dark)}
.main-nav{position:absolute;left:24px;top:167px;list-style:none}
.main-nav li{font-size:21px;line-height:28px;color:var(--gray-nav);text-transform:uppercase}
.connect-title{position:absolute;left:37px;top:334px;font-family:"Carter One",sans-serif;font-size:26px;color:var(--gray-dark)}

.hero{position:absolute;left:318px;top:0;width:844px;height:374px;background:linear-gradient(165deg,var(--hero-dark) 0%,var(--hero-mid) 40%,var(--hero-olive) 75%,var(--hero-light) 100%)}
.contact-top{position:absolute;right:14px;top:8px;display:flex;gap:52px;color:var(--white);font-size:16px}
.steps{position:absolute;left:80px;top:78px;display:flex;gap:22px;font-size:19px;color:#d2d2d2}
.step{display:flex;align-items:center;gap:8px}
.step::before{content:"";width:16px;height:16px;border-radius:50%;background:#d6d6d6}
.step.active{color:var(--green-light)}
.step.active::before{background:var(--green-light)}

.newsletter-band{position:absolute;left:35px;top:376px;width:1130px;height:55px;background:linear-gradient(var(--green-light),var(--green) 60%,var(--green-dark));border:2px solid var(--white);box-shadow:0 1px 3px rgba(0,0,0,.15)}
.social{position:absolute;left:48px;top:8px;display:flex;gap:15px}
.social span{width:38px;height:37px;border-radius:4px;background:linear-gradient(#ffffff,#cfcfcf);border:1px solid #9a9a9a}
.newsletter-text{position:absolute;left:272px;top:13px;font-family:"Tinos",serif;font-style:italic;font-weight:700;font-size:22px;color:var(--white)}
.subscribe-btn{position:absolute;left:758px;top:4px;width:157px;height:43px;border-radius:8px;background:linear-gradient(#ffffff,#e8e8e8);display:flex;align-items:center;justify-content:center;font-family:"Carter One",sans-serif;font-size:19px;color:var(--green-dark)}

.welcome{position:absolute;left:0;width:1180px;top:468px;text-align:center;font-family:"Arvo",serif;font-weight:700;font-size:28px}
.welcome .accent{color:var(--heading-green)}
.welcome .name{color:var(--gray-dark)}
.intro{position:absolute;left:284px;top:533px;width:655px;font-family:"Arimo",sans-serif;font-size:13.5px;line-height:21px;color:var(--gray-text)}
.intro p+p{margin-top:21px}
.quote-btn{position:absolute;left:740px;top:738px;width:202px;height:43px;border-radius:7px;background:linear-gradient(#7cc63a,#3c8c10);box-shadow:0 2px 3px rgba(0,0,0,.3);display:flex;align-items:center;justify-content:center;gap:8px;font-family:"Cinzel",serif;font-weight:600;font-size:23px;color:var(--white)}

.footer{position:absolute;left:0;top:810px;width:1200px;height:143px;border-top:1px solid #eeeeee}
.footer-nav{position:absolute;left:289px;top:47px;display:flex;font-family:"Arimo",sans-serif;font-size:14px;color:#444}
.footer-nav .sep{margin:0 33px 0 28px}
.footer-contact{position:absolute;left:287px;top:91px;display:flex;gap:20px;font-size:15px;color:var(--green)}
.footer-contact .copy{color:#555;font-size:14px}
</style>
</head>
<body>
<div class="canvas">
  <aside class="side-panel">
    <div class="brand">
      <span class="brand-mark"></span>
      <span class="brand-name">MAPLE<br>BEACON</span>
    </div>
    <p class="tagline">Because You´re Awesome!</p>
    <ul class="main-nav">
      <li>Strategy</li>
      <li>Portfolio</li>
      <li>About Us</li>
      <li>Contact Us</li>
      <li>Blog</li>
    </ul>
    <p class="connect-title">Connect with us!</p>
  </aside>

  <section class="hero" role="img" aria-label="Hero photograph: close-up of polished amber and green stones on a soft textured surface">
    <div class="contact-top">
      <span>Email: info@maplebeacon.example</span>
      <span>Phone: 587-555-0142</span>
    </div>
    <div class="steps">
      <span class="step active">Maple Beacon</span>
      <span class="step">Be Found</span>
      <span class="step">Connect</span>
      <span class="step">Get Growing</span>
    </div>
  </section>

  <div class="newsletter-band">
    <div class="social" aria-label="Social links"><span></span><span></span><span></span></div>
    <p class="newsletter-text">Get Tips and Tricks! Subscribe to our Newsletter.</p>
    <div class="subscribe-btn">SUBSCRIBE NOW</div>
  </div>

  <h1 class="welcome"><span class="accent">WELCOME TO</span> <span class="name">MAPLE BEACON</span></h1>
  <div class="intro">
    <p>This is just a bunch of words put toghether to make it look like  paragraph. It is purly for show and filler so that we can have a general idea of what it will ook like when we put in the proper pagaraphs thatmake up our mission statment. I think this font size looks pretty good but maybe be a tad bit smaler.  would like to see the welcome a little more dramatic looking. I think that</p>
    <p>is all I need to write here for now. This is just a bunch of words put toghether to make it look like  paragraph. It is purly for show and filler so that we can have a general idea of what it will ook like when we put in the proper pagaraphs thatmake up our mission statment. I think this font size looks pretty good but maybe be a tad bit smaler.  would like to see the welcome a little more dramatic looking. I think</p>
  </div>
  <div class="quote-btn">FREE QUOTE
    <svg width="12" height="18" viewBox="0 0 12 18"><path d="M0 0 L12 9 L0 18 Z" fill="#ffffff"/></svg>
  </div>

  <footer class="footer">
    <nav class="footer-nav">
      <span>Site Map</span><span class="sep">/</span>
      <span>Strategy</span><span class="sep">/</span>
      <span>Portfolio</span><span class="sep">/</span>
      <span>About Us</span><span class="sep">/</span>
      <span>Contact Us</span><span class="sep">/</span>
      <span>Blog</span>
    </nav>
    <div class="footer-contact">
      <span>Contact info &nbsp;: &nbsp;Email: info@maplebeacon.example</span>
      <span>Phone: 587-555-0142</span>
      <span class="copy">©MAPLE BEACON INC. 2013</span>
    </div>
  </footer>
</div>
</body>
</html>
```